TREVAL BUILDWORKS, LLC Webpage portfolio

I want to create a Website that allows my potential clients to browse my Skilled work via before and after photos. I want the website to enhance the work that I provide and potentially drive new business, or at least solidify my work.
I also do 3D CAD and Modeling of New Spaces and it would be nice to show some of that work from pencil design to 3D modeling, which I feel may help give me more clients.

The website needs to show a solid carpenter/company with the skills to get any project completed.

Types of Jobs - Custom Carpentry & Finishes, Kitchens, Baths, Basements, Decks, Porches, Whole House Renovation - Skilled Craftsmanship (Hardwood Flooring, Floor and Wall Tile) and much more...

Target Market(s)

Residential Home Renovation, Kitchen and Bath Renovation, Home Improvement

Industry/Entity Type

Residential Construction

Number of Pages Required

5+ page

Font styles to use
Sans Serif
Script

Requirements
Must have
• Similar to Plinvo.com, except for Treval Buildworks.
• Must be inviting.
• My Services Offered
• A way to reach me or contact me for estimates with some sort of Screening Questionare.
Nice to have
• Inviting Colors
Should not have
• Not sure at this time

```html
<!DOCTYPE html>
<html lang="en">
<head>
<meta charset="utf-8">
<title>Treval Buildworks — Design, Build &amp; Remodeling</title>
<link href="https://fonts.googleapis.com/css2?family=Michroma&family=Open+Sans:wght@400;600;700&display=swap" rel="stylesheet">
<style>
:root{
  --navy:#0f2c47;
  --navy-deep:#0b2238;
  --blue:#2e9fdc;
  --blue-dark:#1f86c0;
  --indigo:#3f63c8;
  --ink:#1d3550;
  --text:#6f7780;
  --muted:#9aa1a8;
  --bg:#f3f5f7;
  --card:#ffffff;
  --line:#e4e8ec;
  --head:"Michroma", "Open Sans", sans-serif;
  --body:"Open Sans", Arial, sans-serif;
}
*{box-sizing:border-box;margin:0;padding:0}
html,body{width:1200px;height:3529px;overflow:hidden}
body{position:relative;background:var(--bg);font-family:var(--body);color:var(--text)}
.abs{position:absolute}
svg{display:block}

/* header */
.site-header{top:0;left:0;width:1200px;height:104px;background:#fff}
.brand{left:87px;top:18px;display:flex;align-items:center;gap:12px}
.brand-mark{width:26px;height:26px;background:var(--navy)}
.brand-name{font-family:var(--head);font-size:19px;color:var(--navy);line-height:1}
.brand-tag{font-size:8px;letter-spacing:1.6px;color:var(--navy);margin-top:6px}
.search{left:630px;top:29px;display:flex;height:44px}
.search-input{width:377px;border:1px solid var(--line);font-size:12px;color:#a2a8ae;padding:0 14px;display:flex;align-items:center}
.search-btn{width:106px;background:var(--navy);color:#fff;font-size:12px;font-weight:600;display:flex;align-items:center;justify-content:center;letter-spacing:.5px}

/* nav */
.main-nav{top:104px;left:0;width:1200px;height:56px;background:var(--blue)}
.nav-list{position:absolute;left:87px;top:0;height:56px;display:flex;list-style:none}
.nav-list li{height:56px;display:flex;align-items:center;gap:8px;padding:0 29px;color:#fff;font-size:12.5px;letter-spacing:.4px}
.nav-list li.active{background:var(--navy);padding:0 40px}
.nav-list svg{width:13px;height:13px}

/* hero */
.hero{top:160px;left:0;width:1200px;height:525px;background:linear-gradient(180deg,#3a2416 0%,#5b3a22 35%,#4a2d1a 70%,#2b1a10 100%)}
.hero-shade{inset:0;background:rgba(20,12,6,.35)}
.hero-title{top:170px;left:0;width:1200px;text-align:center;font-family:var(--head);font-size:50px;color:#fff}
.hero-text{top:245px;left:390px;width:420px;text-align:center;font-size:13.5px;line-height:1.85;color:#f1ece6}
.hero-actions{top:358px;left:353px;display:flex;gap:8px}
.btn{height:42px;display:flex;align-items:center;justify-content:center;gap:12px;color:#fff;font-size:14px}
.btn-email{width:235px;background:var(--blue)}
.btn-social{width:252px;background:var(--indigo)}
.btn i{width:12px;height:12px;background:#fff;display:block}
.hero-arrow{top:237px;width:54px;height:54px;border:2px solid #fff;border-radius:50%;background:rgba(0,0,0,.2);display:flex;align-items:center;justify-content:center}

/* welcome */
.welcome-title{top:720px;left:0;width:1200px;text-align:center;font-family:var(--head);font-size:23px;color:var(--ink)}
.welcome-title span{color:var(--blue)}
.welcome-sub{top:768px;left:0;width:1200px;text-align:center;font-size:12px}
.feature{top:826px;width:342px;text-align:center}
.feature svg{margin:0 auto;width:90px;height:90px}
.feature h3{font-family:var(--body);font-weight:400;font-size:19px;color:var(--ink);margin-top:22px}
.feature p{font-size:12px;line-height:1.8;margin-top:10px;padding:0 70px}

/* cards */
.card{background:var(--card);box-shadow:0 1px 4px rgba(0,0,0,.07)}
.card-title{font-family:var(--head);font-size:17px;color:var(--ink)}
.copy{font-size:12px;line-height:2.05;color:var(--text)}
.read-more{font-size:12.5px;font-weight:700;color:var(--blue);text-decoration:underline;letter-spacing:.3px}
.photo{display:block}

.model-card{top:1059px;left:87px;width:1026px;height:405px}
.model-card .card-title{position:absolute;left:30px;top:38px;font-size:21px}
.model-card .copy{position:absolute;left:30px;top:92px;width:430px}
.model-card .copy + .copy{top:258px}
.model-card .read-more{position:absolute;left:30px;top:350px}
.model-art{position:absolute;left:478px;top:34px;width:530px;height:318px;background:linear-gradient(135deg,#fafbfc,#e6e9ec 60%,#d3d7db)}

.work-card{width:327px;height:431px}
.work-card .photo{width:327px;height:226px}
.work-card .card-body{padding:18px 14px 0 14px}
.work-card h4{display:flex;align-items:center;gap:12px;font-family:var(--head);font-weight:400;font-size:14px;color:var(--ink)}
.work-card h4 svg{width:14px;height:14px}
.work-card .copy{margin-top:18px;font-size:11.5px;line-height:2.1}
.card-foot{position:absolute;left:14px;right:14px;bottom:16px;display:flex;align-items:center;font-size:11.5px;gap:6px}
.card-foot svg{width:12px;height:12px}
.card-foot .read-more{margin-left:auto;text-decoration:none;font-size:11.5px}
.card-foot .gap{width:12px}

.intro-card .card-title{position:absolute;left:22px;top:36px}
.intro-card .copy{position:absolute;left:22px;width:290px;font-size:11.5px}
.intro-card .read-more{position:absolute;left:22px;top:382px}

.products-card{width:327px;height:431px;display:grid;grid-template-columns:1fr 1fr;padding:16px 12px}
.product{text-align:center;font-size:11.5px;color:var(--text)}
.product .thumb{width:92px;height:70px;margin:8px auto 10px;border-radius:2px}

.ba-card{top:2400px;left:87px;width:677px;height:283px}
.ba-photo{position:absolute;top:28px;width:156px;height:219px}
.ba-tag{position:absolute;bottom:0;left:0;width:74px;height:30px;background:var(--blue);color:#fff;font-size:12px;display:flex;align-items:center;justify-content:center;letter-spacing:.5px}
.ba-card .card-title{position:absolute;left:369px;top:20px;font-size:17px}
.ba-card .copy{position:absolute;left:369px;width:290px;font-size:11.5px;line-height:2.1}

.promo-card{top:2400px;left:786px;width:327px;height:283px;background:linear-gradient(160deg,#3c3e40,#2a2b2c);text-align:center;color:#fff}
.promo-card h3{font-family:var(--head);font-weight:400;font-size:22px;margin-top:42px}
.promo-card p{font-size:12px;line-height:2.05;margin:14px 18px 0;color:#e8e8e8}
.promo-btn{width:150px;height:36px;border:1.5px solid #fff;margin:18px auto 0;font-size:13px;display:flex;align-items:center;justify-content:center;letter-spacing:.5px}

/* partners */
.partners{top:3177px;left:0;width:1200px;height:117px;background:var(--blue)}
.partner-row{position:absolute;left:87px;top:19px;width:1026px;display:flex;justify-content:space-between}
.partner{width:142px;height:80px;border:1px solid rgba(255,255,255,.35);display:flex;align-items:center;justify-content:center;gap:8px;color:#fff;font-size:17px;font-weight:600}
.partner i{width:14px;height:14px;border:2px solid #fff;border-radius:50%;display:block}

/* footer */
.site-footer{top:3294px;left:0;width:1200px;height:235px;background:var(--navy-deep)}
.social{position:absolute;left:0;top:36px;width:1200px;display:flex;justify-content:center;gap:20px}
.social span{width:53px;height:53px;border:1.5px solid rgba(255,255,255,.5);border-radius:50%;display:flex;align-items:center;justify-content:center}
.social span i{width:10px;height:10px;background:#fff;border-radius:50%;display:block}
.foot-nav{position:absolute;left:0;top:128px;width:1200px;display:flex;justify-content:center;list-style:none;font-size:11.5px;color:#dce4ec;letter-spacing:.4px}
.foot-nav li{padding:0 26px;border-left:1px solid rgba(255,255,255,.35);line-height:1}
.foot-nav li:first-child{border-left:0}
.copyright{position:absolute;left:0;top:176px;width:1200px;text-align:center;font-size:11px;color:#b9c4cf}
</style>
</head>
<body>

<header class="site-header abs">
  <div class="brand abs">
    <div class="brand-mark"></div>
    <div>
      <div class="brand-name">Treval Buildworks</div>
      <div class="brand-tag">DESIGN BUILD REMODELING CONTRACTORS</div>
    </div>
  </div>
  <div class="search abs">
    <div class="search-input">Enter Your Keyword.........</div>
    <div class="search-btn">
      <svg width="12" height="12" viewBox="0 0 12 12" style="margin-right:6px"><circle cx="5" cy="5" r="3.6" fill="none" stroke="#fff" stroke-width="1.5"/><line x1="7.6" y1="7.6" x2="11" y2="11" stroke="#fff" stroke-width="1.6"/></svg>SEARCH
    </div>
  </div>
</header>

<nav class="main-nav abs">
  <ul class="nav-list">
    <li class="active"><svg viewBox="0 0 12 12"><path d="M1 6 6 1.5 11 6H9.5v4.5h-2.5V7.5H5v3H2.5V6z" fill="#fff"/></svg>HOME</li>
    <li><svg viewBox="0 0 12 12"><circle cx="6" cy="6" r="5.5" fill="#fff"/><rect x="5.2" y="5" width="1.6" height="4" fill="#2e9fdc"/><circle cx="6" cy="3.4" r=".9" fill="#2e9fdc"/></svg>ABOUT US</li>
    <li><svg viewBox="0 0 12 12"><circle cx="6" cy="6" r="4.2" fill="none" stroke="#fff" stroke-width="2.4" stroke-dasharray="2 1.3"/><circle cx="6" cy="6" r="1.6" fill="#fff"/></svg>SERVICES</li>
    <li><svg viewBox="0 0 12 12"><path d="M1 3.5 6 1l5 2.5v5L6 11 1 8.5z" fill="#fff"/></svg>PRODUCTS</li>
    <li><svg viewBox="0 0 12 12"><path d="M1.5 10.5 2.2 8 8.5 1.7l1.8 1.8L4 9.8z" fill="#fff"/></svg>NEWS</li>
    <li><svg viewBox="0 0 12 12"><rect x="1" y="2" width="10" height="8" fill="none" stroke="#fff" stroke-width="1.4"/><path d="M2.5 8.5 5 6l1.8 1.6L8.5 5.5 9.8 8.5z" fill="#fff"/></svg>GALLERY</li>
    <li><svg viewBox="0 0 12 12"><path d="M3 1h2l1 3-1.5 1a6 6 0 0 0 2.5 2.5L8 6l3 1v2c0 1-1 2-2 2C5 11 1 7 1 3c0-1 1-2 2-2z" fill="#fff"/></svg>CONTACT US</li>
  </ul>
</nav>

<section class="hero abs" role="img" aria-label="Photo of a renovated kitchen with dark wood cabinets, pendant lights and a granite island">
  <div class="hero-shade abs"></div>
  <h1 class="hero-title abs">Treval Buildworks</h1>
  <p class="hero-text abs">Sed ut perspiciatis unde omnis iste natus error sit voluptatem accusantium doloremque laudantium, totam rem aperiam, eaque ipsa quae ab illo inventore veritatis et quasi architecto iste natus error sit beatae vitae dicta sunt explicabo</p>
  <div class="hero-actions abs">
    <div class="btn btn-email"><svg width="14" height="11" viewBox="0 0 14 11"><rect x=".7" y=".7" width="12.6" height="9.6" fill="none" stroke="#fff" stroke-width="1.3"/><path d="M.7 .7 7 6l6.3-5.3" fill="none" stroke="#fff" stroke-width="1.3"/></svg>Sign Up with Email</div>
    <div class="btn btn-social"><i></i>Continue with Linkora</div>
  </div>
  <div class="hero-arrow abs" style="left:25px"><svg width="14" height="18" viewBox="0 0 14 18"><path d="M10 2 3 9l7 7" fill="none" stroke="#fff" stroke-width="2.4"/></svg></div>
  <div class="hero-arrow abs" style="left:1121px"><svg width="14" height="18" viewBox="0 0 14 18"><path d="M4 2l7 7-7 7" fill="none" stroke="#fff" stroke-width="2.4"/></svg></div>
</section>

<h2 class="welcome-title abs">Welcome To <span>Treval Buildworks</span></h2>
<p class="welcome-sub abs">Sed ut perspiciatis unde omnis iste natus error sit voluptatem accusantium doloremque laudantium,totam rem aperiam</p>

<div class="feature abs" style="left:87px">
  <svg viewBox="0 0 90 90" fill="none" stroke="#8a9097" stroke-width="1.6"><rect x="14" y="16" width="62" height="44"/><path d="M36 60v12h18V60M28 74h34"/><path d="M30 48 52 26l6 6-22 22h-6z"/></svg>
  <h3>Discover design ideas</h3>
  <p>Sed ut perspiciatis unde omnis iste natus error sit voluptatem accusantium doloremque</p>
</div>
<div class="feature abs" style="left:429px">
  <svg viewBox="0 0 90 90" fill="none" stroke="#8a9097" stroke-width="1.6"><path d="M24 46a21 21 0 0 1 42 0"/><path d="M18 46h54v6H18z"/><path d="M45 25v-5M38 27l2 12M52 27l-2 12"/><path d="M26 84c2-14 10-20 19-20s17 6 19 20"/></svg>
  <h3>Find home professionals</h3>
  <p>Sed ut perspiciatis unde omnis iste natus error sit voluptatem accusantium doloremque</p>
</div>
<div class="feature abs" style="left:771px">
  <svg viewBox="0 0 90 90" fill="none" stroke="#8a9097" stroke-width="1.6"><path d="M14 42 45 14l31 28"/><path d="M22 36v40h46V36"/><rect x="36" y="52" width="18" height="24"/><rect x="58" y="18" width="7" height="12"/></svg>
  <h3>Shop for your home</h3>
  <p>Sed ut perspiciatis unde omnis iste natus error sit voluptatem accusantium doloremque</p>
</div>

<section class="model-card card abs">
  <h2 class="card-title">3D Modeling</h2>
  <p class="copy">Sed ut perspiciatis unde omnis iste natus error sit voluptatem accusantium doloremque laudantium, totam rem aperiam, eaque ipsa quae ab illo inven tore veritatis et quasi architecto beatae vitae dicta et quasi sunt explicaboSed ut perspiciatis unde omnis iste natus error sit voluptatem accusantium doloremque laudantium, totam rem aperiam, eaque ipsa quae ab illo inventore veritatis et quasi architecto beatae vitae dicta et quasi sunt explicabo</p>
  <p class="copy">Sed ut perspiciatis unde omnis iste natus error sit voluptatem accusan tium doloremque laudantium, totam rem aperiam, eaque ipsa quae ab illo inven tore veritatis et quasi architecto beatae vitae dicta</p>
  <a class="read-more">READ MORE</a>
  <div class="model-art" role="img" aria-label="3D wireframe model of a modern two-storey house"></div>
</section>

<!-- row 1 -->
<article class="work-card card intro-card abs" style="top:1494px;left:87px">
  <h2 class="card-title">Treval Buildworks</h2>
  <p class="copy" style="top:80px">Sed ut perspiciatis unde omnis iste natus error sit voluptatem accusantium doloremque laudantium, totam rem aperiam, eaque ipsa quae ab illo inven tore veritatis et quasi architecto beatae vitae dicta et quasi sunt explicabo</p>
  <p class="copy" style="top:226px">Sed ut perspiciatis unde omnis iste natus error sit voluptatem accusantium doloremque laudantium, totam rem aperiam, eaque ipsa quae ab illo inven tore veritatis et quasi architecto beatae vitae dicta et quasi sunt explicabo</p>
  <a class="read-more">READ MORE</a>
</article>

<article class="work-card card abs" style="top:1494px;left:436px">
  <div class="photo" role="img" aria-label="Custom carpentry kitchen with cherry wood cabinets and island" style="background:linear-gradient(160deg,#5a2d18,#8a4a25 50%,#3b1d10)"></div>
  <div class="card-body"><h4><svg viewBox="0 0 12 12"><path d="M1 11 1.8 8 8.6 1.2l2.2 2.2L4 10.2z" fill="#1d3550"/></svg>Custom Carpentry</h4>
  <p class="copy">Sed ut perspiciatis unde omnis iste natus error sit volup ta tem accusantium doloremque laudantium, totam rem eaque ipsa quae ab illo inventore veritatis</p></div>
  <div class="card-foot"><svg viewBox="0 0 12 12"><path d="M1 1.5h10v7H5l-3 2.5V8.5H1z" fill="none" stroke="#6f7780"/></svg>5<span class="gap"></span><svg viewBox="0 0 12 12"><path d="M6 10.5 1.5 6A2.4 2.4 0 0 1 6 2.8 2.4 2.4 0 0 1 10.5 6z" fill="none" stroke="#6f7780"/></svg>4<a class="read-more">READ MORE</a></div>
</article>

<article class="work-card card abs" style="top:1494px;left:786px">
  <div class="photo" role="img" aria-label="Living room with stone fireplace and built-in wood shelving" style="background:linear-gradient(160deg,#3a2a22,#7a5540 50%,#2a1e18)"></div>
  <div class="card-body"><h4><svg viewBox="0 0 12 12"><path d="M1 11 1.8 8 8.6 1.2l2.2 2.2L4 10.2z" fill="#1d3550"/></svg>Kitchens</h4>
  <p class="copy">Sed ut perspiciatis unde omnis iste natus error sit volup ta tem accusantium doloremque laudantium, totam rem eaque ipsa quae ab illo inventore veritatis</p></div>
  <div class="card-foot"><svg viewBox="0 0 12 12"><path d="M1 1.5h10v7H5l-3 2.5V8.5H1z" fill="none" stroke="#6f7780"/></svg>5<span class="gap"></span><svg viewBox="0 0 12 12"><path d="M6 10.5 1.5 6A2.4 2.4 0 0 1 6 2.8 2.4 2.4 0 0 1 10.5 6z" fill="none" stroke="#6f7780"/></svg>4<a class="read-more">READ MORE</a></div>
</article>

<!-- row 2 -->
<article class="work-card card abs" style="top:1948px;left:87px">
  <div class="photo" role="img" aria-label="Finished room with dark hardwood floor and leather chair" style="background:linear-gradient(160deg,#2a1a12,#5a3a26 50%,#1e130c)"></div>
  <div class="card-body"><h4><svg viewBox="0 0 12 12"><path d="M1 11 1.8 8 8.6 1.2l2.2 2.2L4 10.2z" fill="#1d3550"/></svg>Baths</h4>
  <p class="copy">Sed ut perspiciatis unde omnis iste natus error sit volup ta tem accusantium doloremque laudantium, totam rem eaque ipsa quae ab illo inventore veritatis</p></div>
  <div class="card-foot"><svg viewBox="0 0 12 12"><path d="M1 1.5h10v7H5l-3 2.5V8.5H1z" fill="none" stroke="#6f7780"/></svg>5<span class="gap"></span><svg viewBox="0 0 12 12"><path d="M6 10.5 1.5 6A2.4 2.4 0 0 1 6 2.8 2.4 2.4 0 0 1 10.5 6z" fill="none" stroke="#6f7780"/></svg>4<a class="read-more">READ MORE</a></div>
</article>

<article class="work-card card abs" style="top:1948px;left:436px">
  <div class="photo" role="img" aria-label="Finished basement kitchen with granite bar and wood table" style="background:linear-gradient(160deg,#4a2a1a,#9a6a40 50%,#3a2214)"></div>
  <div class="card-body"><h4><svg viewBox="0 0 12 12"><path d="M1 11 1.8 8 8.6 1.2l2.2 2.2L4 10.2z" fill="#1d3550"/></svg>Basements</h4>
  <p class="copy">Sed ut perspiciatis unde omnis iste natus error sit volup ta tem accusantium doloremque laudantium, totam rem eaque ipsa quae ab illo inventore veritatis</p></div>
  <div class="card-foot"><svg viewBox="0 0 12 12"><path d="M1 1.5h10v7H5l-3 2.5V8.5H1z" fill="none" stroke="#6f7780"/></svg>5<span class="gap"></span><svg viewBox="0 0 12 12"><path d="M6 10.5 1.5 6A2.4 2.4 0 0 1 6 2.8 2.4 2.4 0 0 1 10.5 6z" fill="none" stroke="#6f7780"/></svg>4<a class="read-more">READ MORE</a></div>
</article>

<section class="products-card card abs" style="top:1948px;left:786px">
  <div class="product"><div class="thumb" role="img" aria-label="Bath products" style="background:linear-gradient(135deg,#f2d25a,#d8c8a8)"></div>Baths Products</div>
  <div class="product"><div class="thumb" role="img" aria-label="Kitchen appliances" style="background:linear-gradient(135deg,#d8dadc,#9aa0a6)"></div>Kitchens Products</div>
  <div class="product"><div class="thumb" role="img" aria-label="Basement building blocks" style="background:linear-gradient(135deg,#eceae6,#b8b4ae)"></div>Basements</div>
  <div class="product"><div class="thumb" role="img" aria-label="Mattress and bedroom products" style="background:linear-gradient(135deg,#efe6da,#c9b49a)"></div>Bedroom Products</div>
  <div class="product"><div class="thumb" role="img" aria-label="Hardwood flooring planks" style="background:linear-gradient(135deg,#d79a62,#9a5a2c)"></div>Hardwood Flooring</div>
  <div class="product"><div class="thumb" role="img" aria-label="Floor and wall tile samples" style="background:linear-gradient(135deg,#c4826a,#7a4a3a)"></div>Floor &amp; Wall Tile</div>
</section>

<!-- row 3 -->
<section class="ba-card card abs">
  <div class="ba-photo" role="img" aria-label="Room before renovation with bare framing" style="left:21px;background:linear-gradient(160deg,#8a6a48,#c9a878 50%,#6a4e32)"><span class="ba-tag">BEFORE</span></div>
  <div class="ba-photo" role="img" aria-label="Same room after renovation as a finished kitchen" style="left:186px;background:linear-gradient(160deg,#3a2216,#8a5a34 50%,#2a180e)"><span class="ba-tag">AFTER</span></div>
  <h2 class="card-title">Before and After</h2>
  <p class="copy" style="top:56px">Sed ut perspiciatis unde omnis iste natus error sit vol upta tem accusantium doloremque laudantium, totam eaque ipsa quae ab illo inventore veritatis totam rem accusantium doloremque laudantiumipsa quae ab illo</p>
  <p class="copy" style="top:174px">Sed ut perspiciatis unde omnis iste natus error sit vol upta tem accusantium doloremque laudantium, totam eaque ipsa quae ab illo inventore veritatis</p>
</section>

<section class="promo-card abs" role="img" aria-label="Dark wood floor photo behind product promotion">
  <h3>OUR PRODUCTS</h3>
  <p>Sed ut perspiciatis unde omnis iste natus error sit vol upta tem accusantium doloremque laudantium, tot am eaque ipsa quae ab illo inventoreque</p>
  <div class="promo-btn">VIEW DETAILS</div>
</section>

<!-- row 4 -->
<article class="work-card card abs" style="top:2706px;left:87px">
  <div class="photo" role="img" aria-label="Stacked stone wall with mounted décor and mantel" style="background:linear-gradient(160deg,#4a2e22,#8a5a44 50%,#3a2218)"></div>
  <div class="card-body"><h4><svg viewBox="0 0 12 12"><path d="M1 11 1.8 8 8.6 1.2l2.2 2.2L4 10.2z" fill="#1d3550"/></svg>Decks</h4>
  <p class="copy">Sed ut perspiciatis unde omnis iste natus error sit volup ta tem accusantium doloremque laudantium, totam rem eaque ipsa quae ab illo inventore veritatis</p></div>
  <div class="card-foot"><svg viewBox="0 0 12 12"><path d="M1 1.5h10v7H5l-3 2.5V8.5H1z" fill="none" stroke="#6f7780"/></svg>5<span class="gap"></span><svg viewBox="0 0 12 12"><path d="M6 10.5 1.5 6A2.4 2.4 0 0 1 6 2.8 2.4 2.4 0 0 1 10.5 6z" fill="none" stroke="#6f7780"/></svg>4<a class="read-more">READ MORE</a></div>
</article>

<article class="work-card card abs" style="top:2706px;left:436px">
  <div class="photo" role="img" aria-label="Renovated house interior with light wood doors and white trim" style="background:linear-gradient(160deg,#c9b89a,#e8e0d0 50%,#9a7a54)"></div>
  <div class="card-body"><h4><svg viewBox="0 0 12 12"><path d="M1 11 1.8 8 8.6 1.2l2.2 2.2L4 10.2z" fill="#1d3550"/></svg>Whole House Renovation</h4>
  <p class="copy">Sed ut perspiciatis unde omnis iste natus error sit volup ta tem accusantium doloremque laudantium, totam rem eaque ipsa quae ab illo inventore veritatis</p></div>
  <div class="card-foot"><svg viewBox="0 0 12 12"><path d="M1 1.5h10v7H5l-3 2.5V8.5H1z" fill="none" stroke="#6f7780"/></svg>5<span class="gap"></span><svg viewBox="0 0 12 12"><path d="M6 10.5 1.5 6A2.4 2.4 0 0 1 6 2.8 2.4 2.4 0 0 1 10.5 6z" fill="none" stroke="#6f7780"/></svg>4<a class="read-more">READ MORE</a></div>
</article>

<article class="work-card card abs" style="top:2706px;left:786px">
  <div class="photo" role="img" aria-label="Kitchen with granite counter island and hardwood flooring" style="background:linear-gradient(160deg,#3a2418,#7a5a48 50%,#2a1a10)"></div>
  <div class="card-body"><h4><svg viewBox="0 0 12 12"><path d="M1 11 1.8 8 8.6 1.2l2.2 2.2L4 10.2z" fill="#1d3550"/></svg>Hardwood Flooring</h4>
  <p class="copy">Sed ut perspiciatis unde omnis iste natus error sit volup ta tem accusantium doloremque laudantium, totam rem eaque ipsa quae ab illo inventore veritatis</p></div>
  <div class="card-foot"><svg viewBox="0 0 12 12"><path d="M1 1.5h10v7H5l-3 2.5V8.5H1z" fill="none" stroke="#6f7780"/></svg>5<span class="gap"></span><svg viewBox="0 0 12 12"><path d="M6 10.5 1.5 6A2.4 2.4 0 0 1 6 2.8 2.4 2.4 0 0 1 10.5 6z" fill="none" stroke="#6f7780"/></svg>4<a class="read-more">READ MORE</a></div>
</article>

<section class="partners abs">
  <div class="partner-row">
    <div class="partner">Brightmere</div>
    <div class="partner"><i></i>Velto</div>
    <div class="partner"><i></i>Tunevale</div>
    <div class="partner">Quadrel</div>
    <div class="partner">Corvane</div>
    <div class="partner">Halsey Grid</div>
  </div>
</section>

<footer class="site-footer abs">
  <div class="social">
    <span><i></i></span><span><i></i></span><span><i></i></span><span><i></i></span><span><i></i></span>
    <span><svg width="16" height="12" viewBox="0 0 16 12"><rect x=".7" y=".7" width="14.6" height="10.6" fill="none" stroke="#fff" stroke-width="1.3"/><path d="M.7 .7 8 6.5l7.3-5.8" fill="none" stroke="#fff" stroke-width="1.3"/></svg></span>
  </div>
  <ul class="foot-nav">
    <li>HOME</li><li>ABOUT US</li><li>SERVICES</li><li>PRODUCTS</li><li>NEWS</li><li>GALLERY</li><li>CONTACT US</li>
  </ul>
  <p class="copyright">© Copyrights 2017 Treval Buildworks. All Rights Reserved.</p>
</footer>

</body>
</html>
```